Web Design Project for a Software & Consulting Company

We have just completed a recent ArtHerdly project for a new logo (see attached).
As the next stage of our rebranding we now require a website re-design to complement the new logo.
Our current site, http://www.corvinsoft.example was built in-house and does not come across as professional as we would like. We supply software and associated services to some of the world’s largest oil companies and we need our site to reflect that level of client.
We will also be posting another design project for brochures, PowerPoint slides and other materials very soon.
We would like designs for…
Home page
Product page
• TZQ
• BLV
• PNJ
Services
News page
About Us page
Contact Us page
Page for mobile devices that gives basic company and product information
Currently the site is small but we intend to increase content to include white papers etc. this should be taken into account when designing the navigation therefore we would prefer navigation through styled text links rather than images.
Colour schemes should broadly be taken from our new logo, where the dark blue and dark green from the left and right sides of the logo are the main colours, but other, brighter accent colours can be used to highlight sections or content.
Dark Blue = C:88, M:55, Y:44, K:28
Dark Green = C:87, M:53, Y:50, K:50
NB: Don’t use the logo on our current site, make sure you use the one attached.
We would prefer the final file format to be a layered PSD.
The site should be clean and professional and communicate the following...
• That we have a great depth and breadth of knowledge about our customers’ business, enabling us to deliver the best systems and solutions.
• That we are a leading provider of cost estimation and control solutions to the oil and gas industry.
• The benefits of our software and consulting services.
• Show that we deliver outstanding customer service and value with a very high level of professionalism
• The site should have no Flash and be able to self-adjust to fit any screen size.
Things to avoid …
• Obvious and clichéd oil industry imagery, no oil rigs
• Cartoon style graphics
Our Background
We are an integrated software and consulting organization specialising in the drilling side of the oil and gas industry. Simply put our software helps companies better understand, predict and communicate the cost of drilling wells.
We have 3 software products and a consulting offering consisting of…
• TZQ - Probabilistic time and cost software
• BLV – Cost tracking and reporting software
• PNJ – (currently known as DrillSavant) – Lessons learned software
• Consulting services
Our systems are in use in over 30 countries with a broad range of clients including: GN, Marovel, Dunt, Koruna, VELO Sirkami, FALUMI and Quintex.
Our current site can be found at www.corvinsoft.example
Our main competitors are
• http://www.drovanic.example/
• http://www.sumbrask.example/
• http://www.kve.example/services/software-solutions/p1-
Our depth of drilling knowledge, quality of software and collaboration with clients differentiate us form the competition.
We strive for very high levels of customer service.
We look forward to receiving your designs!
Updates
Thanks to all the designers who have submitted a design, we appreciate the effort.
We will do our best to give individual feedback on each design but given that many are quite similar we thought we would give some general feedback first.
Nearly all the designs submitted so far have been slight variations on…
-
Top Menu
-
Scrolling Photo Banner
-
4 Columns
-
Body
-
Deep Footer
These designs are well executed but they are basically the same layout as our existing site and while there is nothing inherently wrong with this layout we would like to see some designs that are a bit more innovative and different. We don’t really want just a polished version of our current site.
Thanks again,
CVS
Thanks to everyone who has submitted a design, the response has been great.
We are close to making a decision so if you are intending to submit a design please do it soon, the deadline is only a few days away.
Thanks again.
CVS
Target Market(s)
Mid to high level executives
Industry/Entity Type
Oil And Gas
Look and feel

```html
<!DOCTYPE html>
<html lang="en">
<head>
<meta charset="utf-8">
<title>Corvin Software</title>
<link href="https://fonts.googleapis.com/css2?family=Arimo:wght@400;700&display=swap" rel="stylesheet">
<style>
:root{
  --teal-dark:#164450;
  --teal:#1d6577;
  --teal-mid:#225868;
  --accent:#bac47f;
  --grey-band:#eeeeee;
  --text:#555b5e;
  --heading:#1a4a55;
  --white:#ffffff;
}
*{margin:0;padding:0;box-sizing:border-box}
html,body{width:924px;height:1200px;overflow:hidden;background:var(--white);font-family:"Arimo",Arial,sans-serif;color:var(--text)}
.page{position:relative;width:924px;height:1200px}
.abs{position:absolute}

.brand{left:100px;top:46px;display:flex;align-items:center;gap:8px}
.brand-dot{width:34px;height:34px;border-radius:50%;background:var(--teal)}
.brand-name{font-size:17px;font-weight:700;color:var(--heading);line-height:1.05}
.brand-name small{display:block;font-size:8.5px;letter-spacing:3px;font-weight:400;color:var(--heading)}
.search{left:638px;top:28px;width:185px;height:23px;background:var(--teal-dark);border:1px solid #0f2f37;border-radius:3px;color:#dfe7e9;font-size:10px;padding:5px 10px}
.search svg{position:absolute;right:9px;top:5px}
.nav{left:375px;top:77px;width:447px;height:31px;display:flex;border:1px solid #c9cccd;border-radius:3px;background:linear-gradient(#fdfdfd,#e4e6e7)}
.nav a{display:flex;align-items:center;justify-content:center;font-size:9px;font-weight:700;color:var(--heading);text-decoration:none;border-right:1px solid #cfd3d4}
.nav a:last-child{border-right:0}
.nav a.active{background:var(--teal-dark);color:var(--white)}
.dropdown{left:447px;top:108px;width:132px;background:var(--teal-dark);z-index:3}
.dropdown li{list-style:none;height:18.7px;font-size:8.5px;font-weight:700;color:var(--white);padding:5px 0 0 20px;position:relative}
.dropdown li::before{content:"";position:absolute;left:10px;top:7px;border-left:3px solid #fff;border-top:2.5px solid transparent;border-bottom:2.5px solid transparent}
.dropdown li.hover{background:#7f9ca3}

.hero{left:0;top:116px;width:924px;height:312px;background:radial-gradient(ellipse 420px 260px at 300px 150px,#2a8aa0 0%,#1d6577 55%,#164450 100%)}
.hero-art{left:100px;top:55px;width:270px;height:215px;border-radius:6px;background:linear-gradient(135deg,#3e8fd6,#8b9aa5 60%,#3a3f44)}
.hero-title{left:380px;top:133px;width:455px;text-align:center;font-size:27px;font-weight:700;color:var(--white);line-height:30px}
.hero-title em{font-style:normal;color:var(--accent)}
.dots{left:709px;top:261px;display:flex;gap:6px}
.dots span{width:13px;height:13px;border-radius:50%;background:var(--white)}
.dots span.on{background:#8ab53a}

.band{left:0;top:428px;width:924px;height:265px;background:var(--grey-band)}
.card{top:438px;width:161px;height:212px;background:var(--teal-dark);color:var(--white)}
.card h2{height:37px;border-bottom:1px solid #0f3039;font-size:18px;font-weight:700;text-align:center;padding-top:13px;letter-spacing:.5px}
.card-art{width:74px;height:74px;margin:8px auto 0;border-radius:4px}
.card p{font-size:8.8px;line-height:14px;padding:10px 12px 0;text-align:justify}
.btn{top:650px;width:88px;height:20px;background:var(--teal-dark);color:var(--white);font-size:10.5px;font-weight:700;text-align:center;padding-top:4px;border-radius:0 0 3px 3px}
.shadow{top:672px;width:140px;height:4px;border-radius:50%;background:radial-gradient(#cfcfcf,transparent 70%)}

.h-sec{font-size:19px;font-weight:700;color:var(--heading)}
.about-photo{left:99px;top:767px;width:169px;height:102px;border:3px solid #e2e3e3;background:linear-gradient(90deg,#c9ced2,#7d8a93 60%,#e4e8ea)}
.about-text{left:286px;top:766px;width:312px;font-size:9.2px;line-height:14px}
.about-text p+p{margin-top:13px}
.more{font-size:8.5px;color:var(--heading);text-decoration:underline}
.services{left:638px;top:765px;width:186px;font-size:9.2px;line-height:14px}
.services li{list-style:none;padding-left:13px;position:relative}
.services li::before{content:"";position:absolute;left:1px;top:4px;width:6px;height:6px;border-radius:50%;background:var(--teal-dark)}

.clients{left:130px;top:955px;width:660px;height:46px;display:flex;align-items:center;justify-content:space-between}
.clients span{font-size:14px;font-weight:700;color:#3f4a4e}
.arrow{top:968px}

.footer{left:0;top:1020px;width:924px;height:123px;background:var(--teal-dark);color:var(--white)}
.fcol{top:22px;font-size:8px;line-height:14px;white-space:nowrap}
.fcol h3{font-size:9.5px;font-weight:700;margin-bottom:20px}
.badge{left:632px;top:36px;width:190px;height:44px;border-radius:4px;background:#1f5664}
.social{left:100px;top:1162px;display:flex;gap:4px}
.social span{width:23px;height:23px;border-radius:50%;background:#6ea7b3}
.copy{right:102px;top:1166px;font-size:8px;color:#555}
</style>
</head>
<body>
<div class="page">

  <div class="abs brand">
    <span class="brand-dot"></span>
    <div class="brand-name">CORVIN SOFTWARE<small>SOLUTIONS</small></div>
  </div>
  <div class="abs search">Search
    <svg width="11" height="11" viewBox="0 0 11 11"><circle cx="4.5" cy="4.5" r="3.3" fill="none" stroke="#cfd9dc" stroke-width="1.5"/><line x1="7" y1="7" x2="10" y2="10" stroke="#cfd9dc" stroke-width="1.8"/></svg>
  </div>
  <nav class="abs nav">
    <a style="width:72px">HOME</a>
    <a class="active" style="width:97px">PRODUCTS</a>
    <a style="width:79px">SERVICES</a>
    <a style="width:49px">NEWS</a>
    <a style="width:74px">ABOUT US</a>
    <a style="width:76px">CONTACT US</a>
  </nav>
  <ul class="abs dropdown">
    <li>TZQ</li>
    <li class="hover">BLV</li>
    <li>PNJ</li>
  </ul>

  <section class="abs hero">
    <div class="abs hero-art" role="img" aria-label="Hammer and wrench resting on a blueprint"></div>
    <h1 class="abs hero-title"><em>CVS</em> has the better <em>TOOLS</em> to help companies better manage the <em>BUSINESS</em> of <em>DRILLING WELLS</em></h1>
    <div class="abs dots"><span class="on"></span><span></span><span></span><span></span></div>
  </section>

  <div class="abs band"></div>
  <article class="abs card" style="left:100px">
    <h2>PLAN</h2>
    <div class="card-art" role="img" aria-label="Planning documents with calculator and pencil" style="background:linear-gradient(135deg,#f0a43a,#3a8fd0)"></div>
    <p>TZQ delivers a standardized, systematic approach to understanding, quantifying and communicating the impact of project risk to all stakeholders.</p>
  </article>
  <article class="abs card" style="left:286px">
    <h2>EXECUTE</h2>
    <div class="card-art" role="img" aria-label="Tablet showing a checklist" style="background:linear-gradient(135deg,#c7ced3,#3c86cc)"></div>
    <p>Since 1992 BLV has been helping companies optimize their materials and logistics processes and accurately track costs on a daily basis.</p>
  </article>
  <article class="abs card" style="left:474px">
    <h2>LEARN</h2>
    <div class="card-art" role="img" aria-label="Green chalkboard with wooden frame" style="background:linear-gradient(135deg,#d9a77a,#5fae63)"></div>
    <p>DrillSavant is an advanced lessons learned and knowledge management system for use in the Oil &amp; Gas industry. It's fully searchable and easy to use.</p>
  </article>
  <article class="abs card" style="left:661px">
    <h2>EMBED</h2>
    <svg class="card-art" style="display:block" viewBox="0 0 74 74"><path d="M26 22 L14 37 L26 52" fill="none" stroke="#2e9fc8" stroke-width="6" stroke-linejoin="round"/><path d="M48 22 L60 37 L48 52" fill="none" stroke="#2e9fc8" stroke-width="6" stroke-linejoin="round"/><rect x="35" y="20" width="4" height="34" fill="#fff"/></svg>
    <p>Software solutions rely on people and processes to deliver results. From analysis through execution we support our clients to improve performance.</p>
  </article>
  <div class="abs btn" style="left:137px">READ MORE</div>
  <div class="abs btn" style="left:323px">READ MORE</div>
  <div class="abs btn" style="left:510px">READ MORE</div>
  <div class="abs btn" style="left:697px">READ MORE</div>
  <div class="abs shadow" style="left:111px"></div>
  <div class="abs shadow" style="left:297px"></div>
  <div class="abs shadow" style="left:484px"></div>
  <div class="abs shadow" style="left:671px"></div>

  <h2 class="abs h-sec" style="left:99px;top:731px">ABOUT US</h2>
  <div class="abs about-photo" role="img" aria-label="Business team in an office"></div>
  <div class="abs about-text">
    <p>Corvin Software have developed and continue to support software in over 30 countries, providing real results to hundreds of drilling operations.</p>
    <p>With decades of hands-on software and well engineering experience, we are uniquely positioned to provide the right solution to our customers.</p>
  </div>
  <span class="abs more" style="left:286px;top:859px">Read more ...</span>

  <h2 class="abs h-sec" style="left:636px;top:731px">SERVICES</h2>
  <ul class="abs services">
    <li>Process Mapping and Gap Analysis</li>
    <li>Change Management</li>
    <li>Project Management</li>
    <li>Training</li>
    <li>Business and Technical Consulting and</li>
    <li>Support</li>
  </ul>
  <span class="abs more" style="left:638px;top:859px">Read more ...</span>

  <h2 class="abs h-sec" style="left:99px;top:909px">OUR CLIENTS</h2>
  <svg class="abs arrow" style="left:98px" width="14" height="20" viewBox="0 0 14 20"><path d="M11 2 L3 10 L11 18" fill="none" stroke="#444" stroke-width="4"/></svg>
  <div class="abs clients">
    <span>DUNT</span><span>FALUMI</span><span>Marovel</span><span>VELO</span><span>Hardane</span><span>Ostrel</span><span>Pelmar</span><span>GN</span><span>Koruna</span>
  </div>
  <svg class="abs arrow" style="left:808px" width="14" height="20" viewBox="0 0 14 20"><path d="M3 2 L11 10 L3 18" fill="none" stroke="#444" stroke-width="4"/></svg>

  <footer class="abs footer">
    <div class="abs fcol" style="left:99px"><h3>LINKS</h3>Product<br>Services<br>News<br>About us</div>
    <div class="abs fcol" style="left:192px"><h3>SOLUTIONS</h3>Time &amp; Cost Estimation<br>Material &amp; Cost Control<br>Lessons Learned<br>Services &amp; Consulting</div>
    <div class="abs fcol" style="left:316px"><h3>EUROPE</h3>18 Quarry Row<br>Dunmore, DM4 2QT<br>Phone:+44(0)1000 555012<br>Email:eu@corvin.example</div>
    <div class="abs fcol" style="left:426px"><h3>NORTH AMERICA</h3>740 Harbor Point Dr, Suite 210<br>Easton, TX 70010<br>Phone:(555) 010 4471<br>Email:us@corvin.example</div>
    <div class="abs badge" role="img" aria-label="Partner badge"></div>
  </footer>

  <div class="abs social"><span></span><span></span><span></span><span></span></div>
  <div class="abs copy">© 2013 corvinsoftware , All rights reserved.</div>
</div>
</body>
</html>
```